Bramblewood Card Company Business Cards

We are a trading card store with Glimmorax, sports and other TCG cards, we need a business card design that encompasses a clean cut, modern style with a retro flare. website is bramblewoodcardco.com for reference. Can utilize a comic book era feel or a more modern outdoor feel to utilize the "Pacific Northwest" elements of tress, mountains, etc.

Industry/Entity Type

Trading cards and collectibles

Contact Information for Business Card

business name, email address, phone number, name, owner job title

Font styles to use
Sans Serif

```html
<!DOCTYPE html>
<html lang="en">
<head>
<meta charset="utf-8">
<title>Bramblewood Card Company – Business Cards</title>
<link href="https://fonts.googleapis.com/css2?family=Montserrat:wght@500;700;800&family=Roboto:wght@400;500&display=swap" rel="stylesheet">
<style>
  :root {
    --backdrop: #3b3b3b;
    --card-grey: #6e6e6e;
    --ink-grey: #5f5f5f;
    --soft-grey: #8a8a8a;
    --rule: #d6d6d6;
    --accent: #1db3d9;
    --paper: #ffffff;
  }
  * { margin: 0; padding: 0; box-sizing: border-box; }
  html, body { width: 1200px; height: 689px; overflow: hidden; }
  body {
    background: var(--backdrop);
    font-family: "Roboto", Arial, sans-serif;
    position: relative;
  }
  .card {
    position: absolute;
    top: 196px;
    width: 520px;
    height: 297px;
    border-radius: 18px;
    overflow: hidden;
  }
  .card--front { left: 50px; background: var(--card-grey); }
  .card--back { left: 630px; background: var(--paper); }

  .wordmark {
    font-family: "Montserrat", Arial, sans-serif;
    font-weight: 800;
    text-transform: uppercase;
    text-align: center;
    line-height: 1.05;
    letter-spacing: 0.04em;
    white-space: nowrap;
  }
  .card--front .wordmark {
    position: absolute;
    left: 0; right: 0; top: 50%;
    transform: translateY(-50%);
    color: var(--paper);
    font-size: 34px;
  }
  .card--front .wordmark small { display: block; font-size: 19px; letter-spacing: 0.18em; margin-top: 6px; }

  .card--back .wordmark {
    position: absolute;
    right: 40px; top: 48px;
    width: 210px;
    color: var(--ink-grey);
    font-size: 21px;
  }
  .card--back .wordmark small { display: block; font-size: 12px; letter-spacing: 0.2em; margin-top: 5px; }

  .top-rule {
    position: absolute;
    left: 260px; right: 38px; top: 140px;
    border-top: 1px solid var(--rule);
  }
  .person { position: absolute; left: 38px; top: 150px; }
  .person__name { font-family: "Montserrat", Arial, sans-serif; font-weight: 700; color: var(--accent); font-size: 25px; }
  .person__role { color: var(--soft-grey); font-size: 13px; margin-top: 2px; }
  .person__rule { width: 250px; border-top: 1px solid var(--rule); margin: 10px 0 8px; }
  .contact { list-style: none; color: var(--ink-grey); font-size: 13px; }
  .contact li { display: flex; align-items: center; gap: 8px; margin-bottom: 4px; }
  .contact svg { width: 12px; height: 12px; fill: var(--accent); flex: none; }

  .footer-bands { position: absolute; left: 0; bottom: 0; width: 520px; height: 46px; }
  .website {
    position: absolute;
    right: 20px; bottom: 8px;
    color: var(--paper);
    font-size: 12px;
    line-height: 16px;
    letter-spacing: 0.02em;
    white-space: nowrap;
  }
</style>
</head>
<body>
  <section class="card card--front" aria-label="Card front">
    <div class="wordmark">Bramblewood<small>Card Company</small></div>
  </section>

  <section class="card card--back" aria-label="Card back">
    <div class="wordmark">Bramblewood<small>Card Company</small></div>
    <div class="top-rule"></div>

    <div class="person">
      <p class="person__name">Evan Marlow</p>
      <p class="person__role">President</p>
      <div class="person__rule"></div>
      <ul class="contact">
        <li>
          <svg viewBox="0 0 24 24" aria-hidden="true"><path d="M6.6 10.8a15.1 15.1 0 0 0 6.6 6.6l2.2-2.2a1 1 0 0 1 1-.25 11.4 11.4 0 0 0 3.6.57 1 1 0 0 1 1 1V20a1 1 0 0 1-1 1A17 17 0 0 1 3 4a1 1 0 0 1 1-1h3.5a1 1 0 0 1 1 1c0 1.25.2 2.45.57 3.57a1 1 0 0 1-.25 1z"/></svg>
          555-014-2287
        </li>
        <li>
          <svg viewBox="0 0 24 24" aria-hidden="true"><path d="M2 5h20v14H2z M2 5l10 8 10-8"/></svg>
          info@bramblewoodcardco.com
        </li>
      </ul>
    </div>

    <svg class="footer-bands" viewBox="0 0 520 46" aria-hidden="true">
      <path d="M0 40 L282 40 Q290 40 293 32 L297 20 Q300 12 312 12 L520 12 L520 17 L313 17 Q305 17 302 24 L299 34 Q296 46 286 46 L0 46 Z" fill="var(--accent)"/>
      <path d="M292 46 Q300 46 303 36 L306 26 Q309 20 318 20 L520 20 L520 46 Z" fill="var(--ink-grey)"/>
    </svg>
    <p class="website">www.bramblewoodcardco.com</p>
  </section>
</body>
</html>
```